Interior Design/ decoration business card design

This card is for my Interior Design and Decoration business and later I will also be selling homewares. I would like the card to be very simple in design and like either white, duck egg blue , aquas or metallics on a flat mat card excellent quality card. It needs to be well designed as that is my field. I dont like fuss, the simpler the better. I would like a styalised brim under the name brim if possible. SIMPLE, STYLISH, CLASSIC, TASTEFUL

Target Market(s)

40 + year olds who are building or rennovating.

Industry/Entity Type

Business

Contact Information for Business Card

Brim
styling, design, homeware

Marnie Callow
p 0427163958
e marnie@brimhouse.com.au
w brimhouse.com.au

Requirements
Must have
• very simple, stylish, classic, sophisticated. Simple and easy to read text that is a print similar to attached image. I like simple round A's though not as in attached image.

Double sided. It wont save as double sided for some reason!!
Should not have
• not too much colour, No animated / cartoon pictures.

```html
<!DOCTYPE html>
<html lang="en">
<head>
<meta charset="utf-8">
<title>Brim – business card</title>
<link rel="stylesheet" href="https://fonts.googleapis.com/css2?family=Exo+2:wght@300;400;500&display=swap">
<style>
  :root {
    --bg: #e8e5e1;
    --card: #ffffff;
    --brown: #4b3d34;
    --charcoal: #2f2f2f;
    --grey-band: #dedede;
    --grey-strip: #bdbdbd;
    --rule: #8a8a8a;
    --ink: #3a3330;
    --paper-text: #f4f1ee;
  }
  * { box-sizing: border-box; margin: 0; padding: 0; }
  html, body { width: 1200px; height: 675px; overflow: hidden; }
  body {
    background: var(--bg);
    font-family: "Exo 2", sans-serif;
    color: var(--ink);
    position: relative;
  }
  .card {
    position: absolute;
    top: 183px;
    width: 540px;
    height: 309px;
    background: var(--card);
    overflow: hidden;
    box-shadow: 0 6px 18px rgba(0,0,0,.12);
  }
  .card--contact { left: 40px; }
  .card--logo { left: 620px; }

  .corner-stripe {
    position: absolute;
    width: 16px;
    height: 64px;
    background: var(--charcoal);
  }
  .card--contact .corner-stripe { right: 34px; bottom: 0; }
  .card--logo .corner-stripe { left: 34px; bottom: 0; }

  /* timeline rule with nodes */
  .timeline {
    position: absolute;
    left: 63px; top: 18px;
    width: 1.5px; height: 274px;
    background: var(--rule);
  }
  .node {
    position: absolute;
    left: 55px;
    width: 18px; height: 18px;
    border-radius: 50%;
    background: var(--card);
    border: 2px solid var(--rule);
  }
  .node::after {
    content: "";
    position: absolute;
    inset: 3px;
    border-radius: 50%;
    background: #9a9a9a;
  }
  .node--name { top: 61px; }
  .node--web { top: 207px; }

  .tab {
    position: absolute;
    left: 90px;
    background: var(--brown);
    color: var(--paper-text);
  }
  .tab::before {
    content: "";
    position: absolute;
    left: -12px; top: 50%;
    transform: translateY(-50%);
    border-top: 12px solid transparent;
    border-bottom: 12px solid transparent;
    border-right: 12px solid var(--brown);
  }
  .tab--name {
    top: 44px; right: 0; height: 52px;
    padding: 8px 0 0 22px;
  }
  .name {
    font-size: 21px;
    font-weight: 400;
    letter-spacing: 2px;
    text-transform: uppercase;
    line-height: 1.1;
  }
  .role {
    font-size: 11px;
    letter-spacing: 1.6px;
    text-transform: uppercase;
    font-weight: 300;
    margin-top: 3px;
  }

  .details {
    position: absolute;
    left: 90px; right: 0; top: 96px; height: 82px;
    background: var(--grey-band);
    display: flex;
  }
  .icon-strip {
    width: 44px;
    background: var(--grey-strip);
    display: flex;
    flex-direction: column;
    justify-content: space-around;
    align-items: center;
    padding: 5px 0;
  }
  .icon {
    width: 17px; height: 17px;
    border-radius: 50%;
    background: var(--charcoal);
    display: flex; align-items: center; justify-content: center;
  }
  .icon svg { width: 11px; height: 11px; fill: #fff; stroke: none; }
  .detail-list {
    list-style: none;
    display: flex;
    flex-direction: column;
    justify-content: space-around;
    padding: 5px 0 5px 16px;
    font-size: 16px;
    letter-spacing: 1.2px;
    color: var(--ink);
  }

  .tab--web {
    top: 192px; width: 300px; height: 48px;
    display: flex; align-items: center;
    padding-left: 14px; gap: 10px;
  }
  .tab--web .icon-col { display: flex; flex-direction: column; gap: 4px; }
  .tab--web .icon { background: var(--grey-band); width: 16px; height: 16px; }
  .tab--web .icon svg { fill: var(--brown); }
  .web-lines { font-size: 11.5px; letter-spacing: .8px; line-height: 1.55; font-weight: 300; }

  .brand {
    position: absolute;
    inset: 0;
    display: flex; align-items: center; justify-content: center;
  }
  .brand-name {
    font-size: 66px;
    font-weight: 300;
    letter-spacing: 3px;
    color: var(--ink);
  }
</style>
</head>
<body>

  <section class="card card--contact" aria-label="Contact side">
    <div class="timeline"></div>
    <div class="node node--name"></div>
    <div class="node node--web"></div>

    <div class="tab tab--name">
      <p class="name">Marnie Callow</p>
      <p class="role">General Manager</p>
    </div>

    <div class="details">
      <div class="icon-strip">
        <span class="icon"><svg viewBox="0 0 24 24"><path d="M6.6 10.8a15.1 15.1 0 0 0 6.6 6.6l2.2-2.2c.3-.3.7-.4 1-.2 1.1.4 2.3.6 3.6.6.6 0 1 .4 1 1V20c0 .6-.4 1-1 1A17 17 0 0 1 3 4c0-.6.4-1 1-1h3.5c.6 0 1 .4 1 1 0 1.3.2 2.5.6 3.6.1.3 0 .7-.2 1z"/></svg></span>
        <span class="icon"><svg viewBox="0 0 24 24"><path d="M7 3h10v5H7zM4 9h16a2 2 0 0 1 2 2v6h-4v4H6v-4H2v-6a2 2 0 0 1 2-2zm4 7v3h8v-3z"/></svg></span>
        <span class="icon"><svg viewBox="0 0 24 24"><path d="M3 5h18v14H3zm2 2v.5l7 5 7-5V7l-7 5z"/></svg></span>
      </div>
      <ul class="detail-list">
        <li>0427163958</li>
        <li>0427163958</li>
        <li>marnie@brimhouse.com.au</li>
      </ul>
    </div>

    <div class="tab tab--web">
      <div class="icon-col">
        <span class="icon"><svg viewBox="0 0 24 24"><path d="M12 2a10 10 0 1 0 0 20 10 10 0 0 0 0-20zm0 2c1 1.3 1.8 3 2.1 5H9.9C10.2 7 11 5.3 12 4zM4.3 11h3.6c0 1.5.3 3 .8 4.3A8 8 0 0 1 4.3 11zm5.6 0h4.2c0 1.7-.5 3.5-2.1 5.5-1.6-2-2.1-3.8-2.1-5.5zm6.2 0h3.6a8 8 0 0 1-4.4 4.3c.5-1.3.8-2.8.8-4.3z"/></svg></span>
        <span class="icon"><svg viewBox="0 0 24 24"><path d="M12 2a7 7 0 0 0-7 7c0 5 7 13 7 13s7-8 7-13a7 7 0 0 0-7-7zm0 9.5A2.5 2.5 0 1 1 12 6.5a2.5 2.5 0 0 1 0 5z"/></svg></span>
      </div>
      <div class="web-lines">
        <p>brimhouse.com.au</p>
        <p>14 Alder Lane Fitzroy VIC</p>
      </div>
    </div>

    <div class="corner-stripe"></div>
  </section>

  <section class="card card--logo" aria-label="Logo side">
    <div class="brand">
      <p class="brand-name">brim</p>
    </div>
    <div class="corner-stripe"></div>
  </section>

</body>
</html>
```